Business Card Design Project

Business Card
We are rebranding with a new logo
Industry/Entity Type
Business
Contact Information for Business Card
Dennis Morvale +61 487215963 dennis@quorv.com.au P.O. Box 872 Fernlow QLD 4309
Requirements
Must have
- Logo

```html
<!DOCTYPE html>
<html lang="en">
<head>
<meta charset="utf-8">
<title>Quorv International – Business Card</title>
<link rel="stylesheet" href="https://fonts.googleapis.com/css2?family=Exo+2:wght@400;500&display=swap">
<style>
  :root {
    --backdrop: #dcd7cf;
    --card-surface: #eeebe6;
    --card-edge: #d2cdc6;
    --blue-light: #1fa6d6;
    --blue-deep: #15708f;
    --orange-soft: #e98a3a;
    --name-ink: #f3efe4;
    --brand-ink: #1b6d85;
    --contact-ink: #7b7670;
  }
  html, body {
    margin: 0;
    padding: 0;
    width: 1200px;
    height: 1047px;
    overflow: hidden;
    background: var(--backdrop);
    font-family: "Exo 2", sans-serif;
  }
  .card {
    position: absolute;
    left: 100px;
    top: 250px;
    width: 1000px;
    height: 548px;
    border-radius: 22px;
    background: var(--card-surface);
    box-shadow: 0 0 0 1px var(--card-edge), 0 18px 40px rgba(0,0,0,0.12);
    overflow: hidden;
  }
  .accent-panel {
    position: absolute;
    left: 0;
    top: 0;
    width: 360px;
    height: 100%;
    background: linear-gradient(90deg, var(--blue-light) 0%, var(--blue-deep) 82%, var(--orange-soft) 100%);
  }
  .holder-name {
    position: absolute;
    left: 74px;
    top: 84px;
    margin: 0;
    font-weight: 500;
    font-size: 23px;
    line-height: 31px;
    letter-spacing: 0.5px;
    color: var(--name-ink);
    text-transform: uppercase;
  }
  .holder-name span { display: block; }
  .brand {
    position: absolute;
    right: 76px;
    top: 86px;
    text-align: right;
    color: var(--brand-ink);
    font-weight: 500;
  }
  .brand-word {
    display: block;
    font-size: 66px;
    line-height: 74px;
  }
  .brand-sub {
    display: block;
    font-size: 22px;
    letter-spacing: 4px;
    margin-right: -4px;
    margin-top: 4px;
  }
  .contact {
    position: absolute;
    right: 74px;
    top: 386px;
    margin: 0;
    text-align: right;
    font-size: 19px;
    line-height: 30.5px;
    letter-spacing: 1.2px;
    color: var(--contact-ink);
    font-style: normal;
  }
  .contact span { display: block; }
</style>
</head>
<body>
  <section class="card">
    <div class="accent-panel" role="img" aria-label="Blue and orange decorative sweep along the left side of the card"></div>

    <h1 class="holder-name"><span>Dennis</span><span>Morvale</span></h1>

    <div class="brand">
      <span class="brand-word">Quorv</span>
      <span class="brand-sub">INTERNATIONAL</span>
    </div>

    <address class="contact">
      <span>+61 487215963</span>
      <span>dennis@quorv.com.au</span>
      <span>P.O. Box 872 Fernlow QLD 4309</span>
    </address>
  </section>
</body>
</html>
```